Laser Tattoo Removal Business Cards

We are looking for a professional business card design for a laser tattoo removal business. Ideally looking for a black business card design. The name of the business is Brightline Tattoo Removal. We place our cards at local tattoo shops so we ideally are looking for something trendy/edgy to draw both male and female clientele in.

Target Market(s)

Male/Female ages 18-60

Contact Information for Business Card

black background ideally.. hoping to stay within greys, whites and black

Font styles to use
Serif
Sans Serif

Colors
121212
a9a9a9
5c5c5c
f5f5f5
ffffff
7f7f7f
606060
848484
9d9d9d

Requirements
Must have
• Employee Info:
• Melissa Thornbury
• Chief Executive Offer
• m: 919.537.2846
• w: 919.362.4178
• f: 919.685.3907
• mthornbury@brightlinetattooremoval.example
• Address:
• 4615 Oakmere Pkwy, Suite 210
• Raleigh, NC 27654
• Website:
• www.brightlinetattooremoval.example
Nice to have
• Myabe business name on back or logo on back and employee info on the front

```html
<!DOCTYPE html>
<html lang="en">
<head>
<meta charset="utf-8">
<title>Brightline Tattoo Removal – Business Card</title>
<link rel="stylesheet" href="https://fonts.googleapis.com/css2?family=Lato:wght@700&family=Arimo:wght@400;700&display=swap">
<style>
  :root {
    --backdrop: #e6e4e1;
    --gold-light: #d9b48a;
    --gold-mid: #c4955f;
    --gold-dark: #a97a45;
    --ink: #121212;
    --card-black: #000000;
    --white: #ffffff;
    --soft-white: #f5f5f5;
  }
  * { box-sizing: border-box; margin: 0; padding: 0; }
  html, body {
    width: 1200px;
    height: 900px;
    overflow: hidden;
    background: var(--backdrop);
  }
  .canvas {
    position: relative;
    width: 1200px;
    height: 900px;
  }
  .card {
    position: absolute;
    box-shadow: 4px 5px 10px rgba(0, 0, 0, 0.35);
  }
  .card-front {
    left: 330px;
    top: 90px;
    width: 555px;
    height: 343px;
    background: linear-gradient(160deg, var(--gold-light) 0%, var(--gold-mid) 45%, var(--gold-dark) 100%);
    color: var(--ink);
    font-family: "Arimo", Arial, sans-serif;
    text-align: center;
  }
  .holder-name {
    position: absolute;
    top: 63px;
    left: 0;
    width: 100%;
    font-family: "Lato", Arial, sans-serif;
    font-weight: 700;
    font-size: 20px;
    letter-spacing: 0.5px;
  }
  .holder-title {
    position: absolute;
    top: 88px;
    left: 0;
    width: 100%;
    font-size: 15px;
  }
  .rule {
    position: absolute;
    left: 181px;
    width: 198px;
    height: 1px;
    background: var(--ink);
  }
  .rule-top { top: 118px; }
  .rule-bottom { top: 236px; }
  .contact-list {
    position: absolute;
    top: 129px;
    left: 0;
    width: 100%;
    list-style: none;
    font-size: 15px;
    line-height: 23.5px;
  }
  .contact-list b { font-weight: 700; }
  .address {
    position: absolute;
    top: 253px;
    left: 0;
    width: 100%;
    font-size: 15px;
    line-height: 21px;
    font-style: normal;
  }
  .card-back {
    left: 330px;
    top: 469px;
    width: 559px;
    height: 344px;
    background: var(--card-black);
    color: var(--white);
    font-family: "Arimo", Arial, sans-serif;
    text-align: center;
  }
  .brand-name {
    position: absolute;
    top: 150px;
    left: 0;
    width: 100%;
    font-size: 22px;
    font-weight: 400;
    letter-spacing: 3px;
    text-transform: uppercase;
    color: var(--soft-white);
  }
  .website {
    position: absolute;
    top: 287px;
    left: 0;
    width: 100%;
    font-size: 15px;
    color: var(--white);
  }
</style>
</head>
<body>
  <main class="canvas">
    <section class="card card-front" aria-label="Business card front">
      <h1 class="holder-name">MELISSA THORNBURY</h1>
      <p class="holder-title">Chief Executive Officer</p>
      <div class="rule rule-top"></div>
      <ul class="contact-list">
        <li><b>M:</b> 919.537.2846</li>
        <li><b>W:</b> 919.362.4178</li>
        <li><b>F:</b> 919.685.3907</li>
        <li><b>E:</b> mthornbury@brightlinetattooremoval.example</li>
      </ul>
      <div class="rule rule-bottom"></div>
      <address class="address">4615 Oakmere Pkwy, Suite 210<br>Raleigh, NC 27654</address>
    </section>

    <section class="card card-back" aria-label="Business card back">
      <h2 class="brand-name">Brightline Tattoo Removal</h2>
      <p class="website">www.brightlinetattooremoval.example</p>
    </section>
  </main>
</body>
</html>
```